Facebook Post for Fence Spring Sale

We have a $12 / FT Fence sale that we have been running for a while now. We need a flyer made up for SPRING.

Our previous flyer can be seen here:
https://media-cdn4.pixvaultcloud.example/img/v2/58120947_302918475610234_1937465028364719205_n.jpg?k=7c2e91b04d3a58f6e2b7c1d9a0f46e83&t=72A19C04

We want to use the photos that are shown here https://files.boxmeadow.example/share?id=7QxLm2pRtKwZs9VnHyBcJdEf4Ga in the flyer. This is to be posted on Facebook so it must be the proper size for Facebook page post.

The wording to be used should be "Spring Fence Sale" and "$12 / FT Wood Fences" Also we should include our business name "Oakvale Fence" and phone number for Free Estimates - 555-216-4073.

Industry/Entity Type

Residential Construction

Font styles to use
Serif
Sans Serif

Colors
3176b5
fbee3d
fbed22
fbf289
85cae6
33a6d7

Requirements
Must have
• Phone number, $12 / FT Fence Sale

```html
<!DOCTYPE html>
<html lang="en">
<head>
<meta charset="utf-8">
<title>Spring Fence Sale – Oakvale Fence</title>
<link rel="stylesheet" href="https://fonts.googleapis.com/css2?family=Arvo:wght@400;700&family=Archivo+Black&family=Oswald:wght@500&display=swap">
<style>
  :root{
    --backdrop:#e2e2e2;
    --green:#7aa21b;
    --green-dark:#5b6f1c;
    --green-text:#92bb2b;
    --badge-green:#7ea11a;
    --badge-band:#5a7316;
    --sky:#1aa2e0;
    --sky-edge:#64b8e3;
    --white:#ffffff;
    --picket:#e3c99b;
    --picket-shadow:#c6a772;
  }
  *{box-sizing:border-box;margin:0;padding:0}
  html,body{width:1200px;height:1200px;overflow:hidden;background:var(--backdrop)}
  .flyer{position:absolute;left:120px;top:112px;width:976px;height:976px;overflow:hidden;background:#7b8a4a}
  .title-band{position:absolute;left:0;top:0;width:976px;height:80px;background:var(--green);
    display:flex;align-items:center;justify-content:center}
  .title{font-family:"Arvo",serif;font-weight:700;font-size:70px;color:var(--white);letter-spacing:1px;
    text-shadow:3px 3px 4px rgba(0,0,0,.45);margin-left:20px;line-height:1}
  .warranty-band{position:absolute;left:0;top:80px;width:976px;height:44px;background:var(--green-dark);
    display:flex;align-items:center;gap:10px;padding:0 4px}
  .warranty-band .rule{flex:1;height:2px;background:var(--green-text)}
  .warranty{font-family:"Archivo Black",sans-serif;font-size:28px;color:var(--green-text);letter-spacing:3px;line-height:1}
  .photo{position:absolute}
  .picket-strip{position:absolute;left:0;top:476px;width:976px;height:68px;
    background:linear-gradient(180deg,var(--picket),var(--picket-shadow))}
  .footer{position:absolute;left:0;top:852px;width:976px;height:124px;background:var(--sky);
    font-family:"Arvo",serif;color:var(--white);text-shadow:2px 2px 3px rgba(0,0,0,.35)}
  .footer .divider{position:absolute;top:20px;width:2px;height:84px;background:rgba(255,255,255,.85)}
  .inclusions{position:absolute;right:630px;top:20px;text-align:right;font-weight:700;font-size:24px;line-height:41px}
  .brand{position:absolute;left:366px;top:18px;width:236px;text-align:center;font-size:40px;line-height:39px}
  .estimates{position:absolute;left:626px;top:16px;font-size:33px;line-height:40px}
  .badge{position:absolute;left:326px;top:320px;width:316px;height:316px}
  .badge-text{position:absolute;left:326px;top:320px;width:316px;height:316px;text-align:center;color:var(--white);
    text-shadow:2px 2px 3px rgba(0,0,0,.45)}
  .price{position:absolute;left:0;right:0;top:68px;font-family:"Arvo",serif;font-weight:700;font-size:70px;line-height:1}
  .price .unit{font-family:"Oswald",sans-serif;font-weight:500;font-size:54px}
  .wood{position:absolute;left:0;right:0;top:152px;font-family:"Arvo",serif;font-weight:700;font-size:42px;line-height:1;letter-spacing:1px}
  .fences{position:absolute;left:0;right:0;top:194px;font-family:"Oswald",sans-serif;font-weight:500;font-size:64px;line-height:1}
</style>
</head>
<body>
<main class="flyer">
  <header class="title-band"><h1 class="title">SPRING FENCE SALE</h1></header>
  <div class="warranty-band"><span class="rule"></span><span class="warranty">LIFETIME WARRANTY</span><span class="rule"></span></div>

  <div class="photo" role="img" aria-label="Photo of a tall wooden privacy fence with arched top" style="left:0;top:124px;width:194px;height:352px;background:linear-gradient(180deg,#c49a62,#a97d48)"></div>
  <div class="photo" role="img" aria-label="Photo of a dog-ear picket gate with black hinges" style="left:194px;top:124px;width:196px;height:352px;background:linear-gradient(180deg,#d9c6a6,#c2a780)"></div>
  <div class="photo" role="img" aria-label="Photo of a wooden rail fence post on a lawn" style="left:390px;top:124px;width:196px;height:352px;background:linear-gradient(135deg,#4c5a2e,#b89d6e 55%,#6b7d3a)"></div>
  <div class="photo" role="img" aria-label="Photo of a picket fence along a grassy yard" style="left:586px;top:124px;width:196px;height:352px;background:linear-gradient(180deg,#8ea36a,#c8b98a 50%,#6e8a3c)"></div>
  <div class="photo" role="img" aria-label="Photo of a wooden post and wire fence with a company sign" style="left:782px;top:124px;width:194px;height:352px;background:linear-gradient(90deg,#d8c48f 40%,#5f8a3a 60%,#4d7a2f)"></div>

  <div class="picket-strip" role="img" aria-label="Decorative picket fence strip"></div>

  <div class="photo" role="img" aria-label="Photo of a new privacy fence around a backyard" style="left:0;top:544px;width:197px;height:308px;background:linear-gradient(180deg,#5a6038,#d9cfa6 55%,#3f5425)"></div>
  <div class="photo" role="img" aria-label="Photo of a long scalloped privacy fence beside a sidewalk" style="left:197px;top:544px;width:290px;height:308px;background:linear-gradient(90deg,#c7a46a,#b08a52 60%,#5f7a34)"></div>
  <div class="photo" role="img" aria-label="Photo of an arched picket gate set in a rail fence" style="left:487px;top:544px;width:295px;height:308px;background:linear-gradient(180deg,#3f5e2a,#a9b07a 50%,#4e7a2c)"></div>
  <div class="photo" role="img" aria-label="Photo of a stained scalloped privacy fence near houses" style="left:782px;top:544px;width:194px;height:308px;background:linear-gradient(180deg,#b9b2a0,#c9a874 40%,#5e4228)"></div>

  <svg class="badge" viewBox="0 0 316 316" aria-hidden="true">
    <circle cx="158" cy="158" r="150" fill="var(--sky-edge)"/>
    <circle cx="158" cy="158" r="150" fill="none" stroke="var(--sky-edge)" stroke-width="14" stroke-dasharray="10 8"/>
    <circle cx="158" cy="158" r="138" fill="var(--badge-green)"/>
    <path d="M24 82 H292 V140 H24 Z" fill="var(--badge-band)"/>
  </svg>
  <div class="badge-text">
    <div class="price">$12<span class="unit">/FT</span></div>
    <div class="wood">WOOD</div>
    <div class="fences">FENCES</div>
  </div>

  <footer class="footer">
    <p class="inclusions">INCLUDES MATERIALS<br>LABOR AND TAXES!</p>
    <span class="divider" style="left:362px"></span>
    <p class="brand">OAKVALE<br>FENCE</p>
    <span class="divider" style="left:602px"></span>
    <p class="estimates">FREE ESTIMATES:<br>555-216-4073</p>
  </footer>
</main>
</body>
</html>
```